Sonic Vale

Rebrand current website and move it to SonicVale.com. Looking for a professional, eye catching, top 10 in World type website. My current website is: https://madebytorven.sitepadhub.com/sonicvale
I would like it moved to sonicvale.com.

```html
<!DOCTYPE html>
<html lang="en">
<head>
<meta charset="utf-8">
<title>Torven Hale — Sonic Vale</title>
<link rel="stylesheet" href="https://fonts.googleapis.com/css2?family=Oswald:wght@500;600&family=Lato:wght@400;700&family=Montserrat:wght@600;700&display=swap">
<style>
:root{
  --blue:#0b43d6;
  --blue-deep:#0a3cc4;
  --ink:#111111;
  --black:#000000;
  --white:#ffffff;
  --card:#f2f2f2;
  --track:#e6e6e6;
  --line:#777777;
}
*{box-sizing:border-box;margin:0;padding:0}
html,body{width:1200px;height:3569px;overflow:hidden}
body{position:relative;background:var(--white);font-family:"Lato",sans-serif;color:var(--ink)}
.abs{position:absolute}
.center{left:0;width:1200px;text-align:center}
.display{font-family:"Oswald",sans-serif;font-weight:600;text-transform:uppercase}
.accent{color:var(--blue)}
.rule{position:absolute;left:582px;width:36px;height:4px;background:var(--blue)}
.rule.light{background:var(--white)}
.pill{position:absolute;left:502px;width:195px;height:54px;border-radius:27px;display:flex;align-items:center;justify-content:center;gap:12px;font-family:"Montserrat",sans-serif;font-weight:700;font-size:17px;text-transform:uppercase}
.pill.solid{background:var(--blue);color:var(--white);box-shadow:0 6px 14px rgba(11,67,214,.35)}
.pill.ghost{background:var(--white);color:var(--blue)}
.social{display:flex;gap:26px}
.social span{width:32px;height:32px;border-radius:50%;background:var(--blue);display:block}

/* hero */
.hero{top:0;left:0;width:1200px;height:651px;background:radial-gradient(ellipse at 60% 30%,#5a2a1a 0%,#1d2a35 45%,#0a0f16 100%)}
.hero-shade{top:0;left:0;width:1200px;height:651px;background:linear-gradient(180deg,rgba(0,0,0,.55),rgba(0,0,0,.2) 40%,rgba(8,40,70,.35))}
.brand{font-family:"Oswald",sans-serif;font-weight:600;font-size:31px;color:var(--white);text-transform:uppercase}
.nav{display:flex;gap:32px;font-family:"Montserrat",sans-serif;font-weight:700;font-size:12px;color:var(--white);text-transform:uppercase}
.hero-title{top:196px;font-size:46px;color:var(--white)}
.hero-copy{top:278px;left:140px;width:920px;text-align:center;font-size:15px;line-height:30px;color:var(--white)}

/* music */
.section-title{font-size:38px;color:var(--ink)}
.track{top:808px;width:288px;height:356px;background:var(--card);box-shadow:0 4px 10px rgba(0,0,0,.15)}
.track-art{width:288px;height:186px}
.track-name{top:205px;left:0;width:288px;text-align:center;font-family:"Montserrat",sans-serif;font-weight:600;font-size:16px;text-transform:uppercase}
.track-cat{top:234px;left:0;width:288px;text-align:center;font-family:"Montserrat",sans-serif;font-weight:700;font-size:10px;text-transform:uppercase}
.player{top:265px;left:19px;width:250px;height:60px}
.bar{position:absolute;left:50px;top:9px;width:200px;height:8px;border-radius:4px;background:var(--track)}
.bar i{display:block;width:26px;height:8px;border-radius:4px;background:var(--blue)}
.time{position:absolute;top:30px;font-family:"Oswald",sans-serif;font-size:12px;font-weight:500}
.dots{top:1203px;left:570px;display:flex;gap:4px}
.dots span{width:9px;height:9px;border-radius:50%;background:#cfcfcf}
.dots span:first-child{background:var(--blue)}

/* about */
.about{top:1300px;left:0;width:1200px;height:433px;background:linear-gradient(120deg,#1a4fd8,#0c3fcf 55%,#0a37b8)}
.light-text{color:var(--white)}
.about-copy{top:1478px;left:200px;width:800px;text-align:center;font-size:15px;line-height:30px;color:var(--white)}

/* shop */
.product{top:1903px;width:473px;height:390px}
.product-art{width:473px;height:309px}
.product-bar{width:473px;height:81px;background:var(--blue);display:flex;align-items:center;justify-content:space-between;padding:0 33px 0 30px;font-family:"Oswald",sans-serif;font-weight:600;font-size:24px;color:var(--white);text-transform:uppercase}

/* testimonials */
.testimonials{top:2380px;left:0;width:1200px;height:374px;background:linear-gradient(180deg,#1550dc,#0c40cc)}
.avatar{top:2541px;left:506px;width:60px;height:60px;border-radius:50%;background:#4a4f56}
.client{top:2560px;left:579px;font-family:"Montserrat",sans-serif;font-weight:700;font-size:17px;color:var(--white);text-transform:uppercase}
.quote{top:2611px;left:190px;width:820px;text-align:center;font-family:"Oswald",sans-serif;font-weight:500;font-size:24px;line-height:30px;color:var(--white);text-transform:uppercase}

/* form */
.field{position:absolute;border:1px solid var(--line);border-radius:4px;padding:14px 18px;font-size:12px;color:#333}

/* footer */
.footer{top:3278px;left:0;width:1200px;height:291px;background:var(--black)}
.copyright{top:3515px;font-size:13px;color:var(--white)}
</style>
</head>
<body>

<!-- Hero -->
<div class="abs hero" role="img" aria-label="Recording studio with a large mixing console and speaker monitors"></div>
<div class="abs hero-shade"></div>
<div class="abs brand" style="top:16px;left:111px">Torven Hale</div>
<nav class="abs nav" style="top:32px;left:467px"><span>Home</span><span>About</span><span>Shop</span><span>Book Online</span><span>Blog</span></nav>
<div class="abs social" style="top:23px;left:914px" aria-label="Social links"><span></span><span></span><span></span><span></span></div>
<h1 class="abs center display hero-title">Journey with Torven Hale</h1>
<p class="abs hero-copy">Intricate but gritty music producer who specializes in all phases of music production.A a Certified Audio Engineer and a beat maker of genres(hip hop,trap,edm,R&amp;B etc..)I think it’s most important to take pride in quality sound when your involved in any step of the process of creating! Your Music will be professional mixed and mastered to a industry standard.</p>
<div class="pill solid" style="top:388px">Get Started
  <svg width="16" height="16" viewBox="0 0 16 16"><path d="M2 8h10M8 3l5 5-5 5" stroke="#fff" stroke-width="2.6" fill="none" stroke-linecap="round" stroke-linejoin="round"/></svg></div>

<!-- Music -->
<h2 class="abs center display section-title" style="top:724px">Our <span class="accent">Music</span></h2>
<div class="rule" style="top:779px"></div>

<div class="abs track" style="left:125px">
  <div class="track-art" role="img" aria-label="Studio desk with keyboard, headphones and mixer" style="background:linear-gradient(135deg,#3a2a26,#7a5a4a 50%,#2a201c)"></div>
  <div class="abs track-name">Trap Trap Torven</div>
  <div class="abs track-cat">Shop</div>
  <div class="abs player">
    <svg class="abs" style="left:0;top:-8px" width="42" height="42" viewBox="0 0 42 42"><circle cx="21" cy="21" r="21" fill="#0b43d6"/><rect x="15" y="14" width="4" height="14" fill="#fff"/><rect x="23" y="14" width="4" height="14" fill="#fff"/></svg>
    <div class="bar"><i></i></div>
    <span class="time" style="left:50px">00.02</span><span class="time" style="right:0">04:16</span>
  </div>
</div>
<div class="abs track" style="left:456px">
  <div class="track-art" role="img" aria-label="Close view of mixing console faders" style="background:linear-gradient(135deg,#2a1a22,#6a4a5a 50%,#1c1218)"></div>
  <div class="abs track-name">A List Torven</div>
  <div class="abs track-cat">Shop</div>
  <div class="abs player">
    <svg class="abs" style="left:0;top:-8px" width="42" height="42" viewBox="0 0 42 42"><circle cx="21" cy="21" r="21" fill="#0b43d6"/><rect x="15" y="14" width="4" height="14" fill="#fff"/><rect x="23" y="14" width="4" height="14" fill="#fff"/></svg>
    <div class="bar"><i></i></div>
    <span class="time" style="left:50px">00.02</span><span class="time" style="right:0">03:59</span>
  </div>
</div>
<div class="abs track" style="left:787px">
  <div class="track-art" role="img" aria-label="Studio control room with screens and monitors" style="background:linear-gradient(135deg,#0e2a36,#2a6a7a 50%,#0a1a22)"></div>
  <div class="abs track-name">Element Torven</div>
  <div class="abs track-cat">Shop</div>
  <div class="abs player">
    <svg class="abs" style="left:0;top:-8px" width="42" height="42" viewBox="0 0 42 42"><circle cx="21" cy="21" r="21" fill="#0b43d6"/><rect x="15" y="14" width="4" height="14" fill="#fff"/><rect x="23" y="14" width="4" height="14" fill="#fff"/></svg>
    <div class="bar"><i></i></div>
    <span class="time" style="left:50px">00.02</span><span class="time" style="right:0">03:24</span>
  </div>
</div>
<div class="abs dots"><span></span><span></span><span></span><span></span><span></span></div>

<!-- About -->
<div class="abs about" role="img" aria-label="Blue-tinted studio background with headphones and waveforms"></div>
<h2 class="abs center display light-text" style="top:1372px;font-size:38px">About Us</h2>
<div class="rule light" style="top:1426px"></div>
<div class="abs center display light-text" style="top:1448px;font-size:17px">A Life Steeped in Sound</div>
<p class="abs about-copy">Hailing from New Orleans, Torven has always pushed himself to achieve more success in his music career. Looking to perfect his technical abilities and develop his own unique style, Torven draws upon his New Orleans roots and lifelong passion for music. Get in touch to learn more about his background, experience, and latest projects.</p>
<div class="pill ghost" style="top:1592px">Get in Touch
  <svg width="16" height="16" viewBox="0 0 16 16"><path d="M2 8h10M8 3l5 5-5 5" stroke="#0b43d6" stroke-width="2.6" fill="none" stroke-linecap="round" stroke-linejoin="round"/></svg></div>

<!-- Shop -->
<h2 class="abs center display section-title" style="top:1806px">Our <span class="accent">Shop</span></h2>
<div class="rule" style="top:1861px"></div>
<div class="abs product" style="left:111px">
  <div class="product-art" role="img" aria-label="Producer in headphones working at a studio computer" style="background:linear-gradient(135deg,#0e3a44,#1f5a66 50%,#2a1a1a)"></div>
  <div class="product-bar"><span>Mixing and Mastering</span><span>$ 150.00</span></div>
</div>
<div class="abs product" style="left:617px">
  <div class="product-art" role="img" aria-label="Lit mixing desk faders and knobs" style="background:linear-gradient(135deg,#1a2a4a,#8a8a7a 50%,#3a4a5a)"></div>
  <div class="product-bar"><span>Book a Session</span><span>$ 120.00</span></div>
</div>

<!-- Testimonials -->
<div class="abs testimonials" role="img" aria-label="Blue-tinted mixing console background"></div>
<h2 class="abs center display light-text" style="top:2454px;font-size:38px">Our Client Testimonials</h2>
<div class="rule light" style="top:2509px;left:582px"></div>
<div class="abs avatar" role="img" aria-label="Client portrait"></div>
<div class="abs client">Marcel Duvane</div>
<p class="abs quote">“Music expresses that which cannot be said and on which it is impossible to be silent”</p>

<!-- Contact -->
<h2 class="abs center display section-title" style="top:2828px">Get <span class="accent">In Touch</span></h2>
<div class="rule" style="top:2883px"></div>
<div class="field" style="top:2913px;left:202px;width:393px;height:46px">First name</div>
<div class="field" style="top:2913px;left:606px;width:392px;height:46px">Last name</div>
<div class="field" style="top:2973px;left:202px;width:393px;height:46px">Email</div>
<div class="field" style="top:2973px;left:606px;width:392px;height:46px">Phone</div>
<div class="field" style="top:3033px;left:202px;width:796px;height:113px">Message</div>
<div class="pill solid" style="top:3170px;gap:34px">Submit
  <svg width="16" height="16" viewBox="0 0 16 16"><path d="M2 8h10M8 3l5 5-5 5" stroke="#fff" stroke-width="2.6" fill="none" stroke-linecap="round" stroke-linejoin="round"/></svg></div>

<!-- Footer -->
<footer class="abs footer"></footer>
<div class="abs center brand" style="top:3358px;font-size:34px">Torven Hale</div>
<nav class="abs nav" style="top:3430px;left:423px"><span>Home</span><span>About</span><span>Shop</span><span>Book Online</span><span>Blog</span></nav>
<div class="abs social" style="top:3466px;left:513px;gap:15px"><span></span><span></span><span></span><span></span></div>
<div class="abs center copyright">© copyrights 2021 Torven Hale &nbsp;&nbsp;| &nbsp;&nbsp;&nbsp;All rights reserved.</div>

</body>
</html>
```